TK Stationery - Modern Contemporary

Develop modern template for Letterhead and Stationery (business card, letterhead, envelopes) using the TK Logo and Icon

Colors
0054AA
0677BA
7BADD7
CADEEF
E8F1F8
00AB8E
00BBA5
67D7C9
C6EFE9
E9F9F6
EE7325
F08F49
F5BC92
FAE3D3
FDF4ED
6B429C
8869AF
B7A5CE
E3DAEB
F3F0F8

```html
<!DOCTYPE html>
<html lang="en">
<head>
<meta charset="utf-8">
<title>Tela Kora Stationery</title>
<link href="https://fonts.googleapis.com/css2?family=Questrial&display=swap" rel="stylesheet">
<style>
  :root{
    --backdrop:#a9a9a9;
    --paper:#ffffff;
    --paper-shade:#e9e9e9;
    --navy:#2a2e4a;
    --green:#1fc174;
    --orange:#f4862a;
    --text:#4a4d5c;
    --white:#ffffff;
  }
  *{box-sizing:border-box;margin:0;padding:0}
  html,body{width:1200px;height:806px;overflow:hidden}
  body{background:var(--backdrop);font-family:"Questrial",sans-serif;color:var(--text);position:relative}

  .sheet{position:absolute;background:linear-gradient(90deg,var(--paper) 0%,var(--paper) 45%,var(--paper-shade) 100%);box-shadow:0 2px 6px rgba(0,0,0,.18);overflow:hidden}

  .wordmark{font-family:"Questrial",sans-serif;font-weight:400;color:var(--navy);letter-spacing:.5px;white-space:nowrap;line-height:1}

  /* letterhead */
  .letterhead{left:76px;top:108px;width:450px;height:631px}
  .letterhead .wordmark{position:absolute;left:48px;top:70px;font-size:30px}
  .contact{position:absolute;left:288px;top:40px;list-style:none;font-size:9.4px;line-height:11.5px;color:#5a5d6a}
  .contact li{display:flex;align-items:flex-start;gap:6px;margin-bottom:3.2px}
  .contact li.address{margin-bottom:6px}
  .contact svg{flex:none;width:10px;height:10px;margin-top:1px}
  .salutation{position:absolute;left:41px;top:176px;font-size:11.5px;color:#3b3e4d}
  .body-copy{position:absolute;left:41px;top:209px;width:372px;font-size:6.2px;line-height:9.6px;text-align:justify;color:#5b5e6b}
  .body-copy p{margin-bottom:9.6px}
  .closing{position:absolute;left:41px;top:413px;font-size:6.4px;color:#5b5e6b}
  .wave{position:absolute;left:0;bottom:0;width:100%}
  .letterhead .wave{height:58px}

  /* envelope back views */
  .envelope-back{width:517px;height:236px}
  .envelope-back.green-flap{left:609px;top:115px}
  .envelope-back.navy-flap{left:568px;top:236px}
  .flap{position:absolute;left:0;top:0;width:100%;height:74px}
  .flap .wordmark{position:absolute;left:0;right:0;top:28px;text-align:center;font-size:21px;color:var(--white)}

  /* envelope front */
  .envelope-front{left:567px;top:504px;width:518px;height:235px}
  .envelope-front .wordmark{position:absolute;left:39px;top:36px;font-size:28px}
  .return-address{position:absolute;left:39px;top:68px;font-size:9.4px;line-height:11.5px;color:#5a5d6a}
  .envelope-front .wave{height:52px}
</style>
</head>
<body>

<!-- Letterhead -->
<section class="sheet letterhead">
  <div class="wordmark">tela kora</div>

  <ul class="contact">
    <li class="address">
      <svg viewBox="0 0 10 10"><circle cx="5" cy="5" r="5" fill="var(--orange)"/><path d="M5 2.2a1.8 1.8 0 0 0-1.8 1.8C3.2 5.4 5 7.8 5 7.8S6.8 5.4 6.8 4A1.8 1.8 0 0 0 5 2.2z" fill="var(--white)"/><circle cx="5" cy="4" r=".6" fill="var(--orange)"/></svg>
      <span>4120 Larkspur Way<br>Halden, Oregon 97310</span>
    </li>
    <li>
      <svg viewBox="0 0 10 10"><circle cx="5" cy="5" r="5" fill="var(--orange)"/><path d="M3.3 2.6l1 1-.6.7a3.6 3.6 0 0 0 2 2l.7-.6 1 1-.8.8C4.9 7.4 2.6 5.1 2.5 3.4z" fill="var(--white)"/></svg>
      <span>555-014-2287</span>
    </li>
    <li>
      <svg viewBox="0 0 10 10"><circle cx="5" cy="5" r="5" fill="var(--orange)"/><rect x="3.5" y="2.2" width="3" height="5.6" rx=".5" fill="var(--white)"/><rect x="4" y="3" width="2" height="3.6" fill="var(--orange)"/></svg>
      <span>555-019-3346</span>
    </li>
    <li>
      <svg viewBox="0 0 10 10"><circle cx="5" cy="5" r="5" fill="var(--orange)"/><rect x="2.6" y="3.3" width="4.8" height="3.4" fill="var(--white)"/><path d="M2.6 3.3L5 5.2l2.4-1.9" fill="none" stroke="var(--orange)" stroke-width=".5"/></svg>
      <span>name@telakora.com</span>
    </li>
    <li>
      <svg viewBox="0 0 10 10"><circle cx="5" cy="5" r="5" fill="var(--orange)"/><circle cx="5" cy="5" r="2.3" fill="none" stroke="var(--white)" stroke-width=".7"/><path d="M2.7 5h4.6M5 2.7v4.6" stroke="var(--white)" stroke-width=".5"/></svg>
      <span>www.telakora.com</span>
    </li>
  </ul>

  <p class="salutation">Dear Mr. Harlow,</p>

  <div class="body-copy">
    <p>Lorem ipsum dolor sit amet, consectetur adipiscing elit. Donec orci purus, luctus vitae dignissim eu, iaculis sed purus. Vivamus faucibus, ipsum nec aliquet viverra, leo mauris condimentum ligula, sit amet sagittis enim ligula quis arcu. Nam egestas tortor id nisi porttitor mattis. In tortor ante, ultricies in suscipit a, tempus non massa. Vivamus et auctor mi. Fusce vel massa nulla. Phasellus nec eros mauris, et scelerisque orci.</p>
    <p>Donec malesuada orci vitae nulla accumsan porta a id massa. Quisque accumsan iaculis magna sit amet fringilla. Maecenas consequat, magna eget tincidunt semper, odio nibh rutrum mi, id feugiat ante nisi eu risus. Vestibulum nunc orci, rhoncus a placerat in, ultricies in mi. Cras mattis varius eros, vel fringilla nisi suscipit eget. Quisque scelerisque sagittis nulla at porttitor.</p>
    <p>Sed id augue vitae urna euismod commodo aliquet a quam. Pellentesque arcu velit, cursus et malesuada ut, consequat et diam. Nullam erat sem, rhoncus id ullamcorper vitae, rhoncus et arcu. In ultricies ultricies nulla, ut rutrum nisl iaculis at. Donec eu magna a metus ornare faucibus. Fusce aliquet faucibus ultricies. Morbi semper, est id tincidunt gravida, sem arcu adipiscing lacus, ac bibendum nulla leo eu purus. Quisque nec diam sed risus consectetur a accumsan quis quis nibh. Vestibulum id purus lorem.</p>
    <p>It is a long established fact that a reader will be distracted by the readable content of a page when looking at its layout. The point of using Lorem Ipsum is that it has a more-or-less normal distribution of letters, as opposed to using 'Content here, content here', making it look like readable English. Many desktop publishing packages</p>
  </div>

  <p class="closing">Sincerely,</p>

  <svg class="wave" viewBox="0 0 450 60" preserveAspectRatio="none" aria-hidden="true">
    <path d="M0 4C90 44 200 42 300 24C370 12 420 16 450 36V60H0Z" fill="var(--green)"/>
    <path d="M0 12C90 50 200 46 300 28C370 17 420 20 450 40V60H0Z" fill="var(--white)"/>
    <path d="M0 15C90 52 200 48 300 31C370 21 420 24 450 44V60H0Z" fill="var(--orange)"/>
    <path d="M0 19C90 55 200 51 300 36C370 27 420 30 450 49V60H0Z" fill="var(--navy)"/>
  </svg>
</section>

<!-- Envelope back, green flap -->
<section class="sheet envelope-back green-flap">
  <div class="flap">
    <svg viewBox="0 0 517 74" width="517" height="74" preserveAspectRatio="none" aria-hidden="true">
      <path d="M0 0H517L508 52Q504 74 480 74H37Q13 74 9 52Z" fill="var(--green)"/>
    </svg>
    <div class="wordmark">tela kora</div>
  </div>
</section>

<!-- Envelope back, navy flap -->
<section class="sheet envelope-back navy-flap">
  <div class="flap">
    <svg viewBox="0 0 517 74" width="517" height="74" preserveAspectRatio="none" aria-hidden="true">
      <path d="M0 0H517L508 52Q504 74 480 74H37Q13 74 9 52Z" fill="var(--navy)"/>
    </svg>
    <div class="wordmark">tela kora</div>
  </div>
</section>

<!-- Envelope front -->
<section class="sheet envelope-front">
  <div class="wordmark">tela kora</div>
  <p class="return-address">4120 Larkspur Way<br>Halden, Oregon 97310</p>
  <svg class="wave" viewBox="0 0 450 60" preserveAspectRatio="none" aria-hidden="true">
    <path d="M0 4C90 44 200 42 300 24C370 12 420 16 450 36V60H0Z" fill="var(--green)"/>
    <path d="M0 12C90 50 200 46 300 28C370 17 420 20 450 40V60H0Z" fill="var(--white)"/>
    <path d="M0 15C90 52 200 48 300 31C370 21 420 24 450 44V60H0Z" fill="var(--orange)"/>
    <path d="M0 19C90 55 200 51 300 36C370 27 420 30 450 49V60H0Z" fill="var(--navy)"/>
  </svg>
</section>

</body>
</html>
```